Belvascotravel.com web design project + logo design

Hi,

We are a Russian online tour operator - sunkettle.com

We are looking to tranmsfer our domain to belvascotravel.com. The website and logo need to be belvascoesque - we are not looking to change our functionality, but we need to make the website much more attracitve to clients, much more wild looking but at the same time remaining a professional travel company.

The main concept of the website should be innovative travel (as belvasco was an innovator). Alternatively, you could go down the artist route and go down the draw / design your own tour road.

On our website the customer is able to combine travel services (hotels, flights, Visa services, and soon chauffeur, car rental etc...) put it into their basket (the basket definitely has to look better than it is at the moment) and pay for it in one go by card.

We are also stressin our customer support with web chat, call centre etc... (call centre number at the top of the page)

We aim to provide an easy user experience, but we need to make it have some more style, so I will be waiting for what you guys can come up with.
Let me know if you have any questions - skype is: mrdolbarin

Industry/Entity Type

It Company

Requirements
Must have
• It is quite a simple task - to take the existing website sunkettle.com and belvascosize it to create belvascotravel.com, the functionality of the website will remain the same and there are not many pages in the website. Homepage, Checkout step1, Checkout step 2 (you can view both of these if you select a service) and the generic pages for T&C''s, Privacy policy etc...

IMPORTANT UPDATE

We are also looking at how the search results will look in the designs, (please do a search on our website for hotel / flight)

```html
<!DOCTYPE html>
<html lang="en">
<head>
<meta charset="utf-8">
<title>Belvasco Travel</title>
<link href="https://fonts.googleapis.com/css2?family=Open+Sans:wght@400;600;700&display=swap" rel="stylesheet">
<style>
:root{
  --page:#ececec;
  --footer:#e6e4e4;
  --text:#555;
  --dark:#111;
  --gold:#d6a516;
  --green:#7fb51a;
  --green-text:#7aa51a;
  --purple:#a30ab8;
  --purple-light:#c313d8;
  --orange:#f5a623;
  --violet:#8a44c0;
  --hotel:#139e1a;
  --white:#fff;
}
*{margin:0;padding:0;box-sizing:border-box}
html,body{width:1200px;height:990px;overflow:hidden}
body{position:relative;background:var(--page);font-family:"Open Sans",Arial,sans-serif;color:var(--text)}
.abs{position:absolute}

.hero{left:0;top:110px;width:1200px;height:470px;
  background:linear-gradient(180deg,var(--page) 0%,#cfc6b8 12%,#b9906a 30%,#c9873e 48%,#a86b2e 62%,#556b2a 80%,#3f5a22 100%)}
.slider-dots{left:130px;top:413px;display:flex;gap:8px}
.slider-dots span{width:12px;height:12px;border-radius:50%;background:#9a9a9a;border:1px solid #666}

.brand{left:120px;top:46px;font-family:"Open Sans",Arial,sans-serif;font-weight:700;font-size:27px;letter-spacing:.3px;color:var(--gold)}
.contacts{right:121px;top:26px;text-align:right;font-size:15.5px;line-height:25px}
.contacts .phone{color:var(--green-text)}
.contacts .hours{color:var(--dark);font-size:14.5px}

.nav{left:120px;top:121px;width:960px;height:40px;display:flex;background:linear-gradient(#8cc21e,#6ea312)}
.nav a{color:var(--white);text-decoration:none;font-size:14.5px;line-height:38px;text-transform:uppercase}
.nav .links{display:flex;width:710px;padding-left:21px}
.nav .links a:nth-child(1){width:105px}
.nav .links a:nth-child(2){width:135px}
.nav .links a:nth-child(3){width:129px}
.nav .links a:nth-child(4){width:111px}
.nav .links a:nth-child(5){width:114px}
.my-tour{width:117px;background:var(--gold);display:flex;align-items:center;gap:8px;padding-left:14px;color:var(--white);font-size:14.5px}
.lang{width:133px;background:var(--gold);padding:4px 6px 4px 0}
.lang .box{background:var(--white);height:32px;display:flex;align-items:center;padding-left:8px;gap:10px;font-size:12px;color:#222}
.lang .flag{width:24px;height:16px;background:#3a4a9a}

.tabs{left:120px;top:449px;display:flex;height:36px}
.tab{color:var(--white);font-size:15px;line-height:40px;text-align:center;text-transform:uppercase}
.tab.t-tickets{width:94px;background:var(--purple)}
.tab.t-info{width:76px;background:var(--gold)}
.tab.t-hotels{width:96px;background:var(--green)}

.basket{left:677px;top:444px;width:403px;height:41px;background:var(--gold);border-radius:3px 3px 0 0;display:flex;align-items:center;padding-left:10px;color:var(--white)}
.basket .title{font-size:15px;margin-left:8px}
.basket .title b{color:var(--dark);font-weight:400}
.checkout{margin-left:28px;background:#f5c51e;border:1px solid #e9b000;color:#8a6a00;font-size:12px;padding:4px 8px;border-radius:3px}
.pricing{margin-left:10px;font-size:11.5px;font-weight:700}

.search{left:120px;top:485px;width:960px;height:160px;border-radius:0 0 3px 3px;background:linear-gradient(var(--purple),var(--purple-light))}
.label{color:var(--white);font-size:12px;font-weight:600;text-transform:uppercase}
.field{height:33px;background:linear-gradient(#fff,#e8e8e8);border-radius:3px;box-shadow:inset 2px 2px 4px rgba(0,0,0,.35);font-size:12px;color:#999;display:flex;align-items:center;padding-left:12px}
.field .ctl{margin-left:auto;width:32px;height:20px;border-left:1px solid #ccc;display:flex;align-items:center;justify-content:center}
.submit{left:833px;top:115px;width:112px;height:36px;border-radius:4px;background:linear-gradient(#f049f5,#c313d8);border:1px solid #e06ae8;color:var(--white);font-size:15px;text-align:center;line-height:34px}

.feature{top:679px;width:300px}
.feature .head{display:flex;align-items:center;gap:18px;height:36px}
.feature .icon{width:36px;height:36px;border-radius:4px;display:flex;align-items:center;justify-content:center}
.feature h2{font-weight:400;font-size:21px;text-transform:uppercase}
.feature .rule{height:6px;margin-top:11px;margin-bottom:10px}
.feature p{font-size:11px;line-height:18px;text-align:justify;color:var(--text)}
.feature ol{list-style:none;font-size:12px;line-height:22px;margin-top:6px;color:#444}
.visa{left:120px}.visa h2{color:var(--orange)}.visa .rule,.visa .icon{background:var(--orange)}
.tickets{left:449px}.tickets h2{color:var(--violet)}.tickets .rule,.tickets .icon{background:var(--violet)}
.hotels{left:780px}.hotels h2{color:var(--hotel)}.hotels .rule,.hotels .icon{background:var(--hotel)}

.footer{left:0;top:923px;width:1200px;height:67px;background:var(--footer);border-top:1px solid #d4d4d4}
.footer-links{left:121px;top:13px;font-size:11px;color:#555}
.footer-links a{color:#555;text-decoration:none}
.footer-links span{margin:0 3px}
.copyright{left:121px;top:37px;font-size:11px;color:#555}
.social{left:896px;top:11px;display:flex;gap:18px}
.social span{width:32px;height:32px;background:#8e8e8e;border-radius:2px}
</style>
</head>
<body>

<div class="abs hero" role="img" aria-label="Panoramic photo of a hilltop fortress palace with towers among trees, mountains behind at sunset"></div>
<div class="abs slider-dots"><span></span><span></span><span></span></div>

<div class="abs brand">BELVASCOTRAVEL</div>
<div class="abs contacts">
  <div class="phone">8-800-555-0142</div>
  <div class="phone">+7 (495) 555-01-87</div>
  <div class="hours">(Mon-Fri) Hours: 9:00 am - 18:00</div>
</div>

<nav class="abs nav">
  <div class="links">
    <a href="#">Home</a><a href="#">About us</a><a href="#">Services</a><a href="#">Places</a><a href="#">Forum</a><a href="#">Contacts</a>
  </div>
  <div class="my-tour">
    <svg width="14" height="16" viewBox="0 0 14 16"><circle cx="7" cy="4.5" r="3.5" fill="#fff" opacity=".85"/><path d="M0 16c0-5 3-7 7-7s7 2 7 7z" fill="#fff" opacity=".85"/></svg>
    MY TOUR
  </div>
  <div class="lang"><div class="box"><span class="flag"></span>ENGLISH
    <svg style="margin-left:14px" width="12" height="9" viewBox="0 0 12 9"><path d="M0 0h12L6 9z" fill="#999"/></svg></div></div>
</nav>

<div class="abs tabs">
  <div class="tab t-tickets">Tickets</div>
  <div class="tab t-info">Info</div>
  <div class="tab t-hotels">Hotels</div>
</div>

<div class="abs basket">
  <svg width="30" height="24" viewBox="0 0 30 24"><path d="M1 3h5l4 13h15l3-10H8" fill="none" stroke="#3c9a1a" stroke-width="2.2"/><circle cx="12" cy="21" r="2" fill="#3c9a1a"/><circle cx="23" cy="21" r="2" fill="#3c9a1a"/></svg>
  <span class="title">MY BASKET <b>(0)</b></span>
  <span class="checkout">CHECKOUT</span>
  <span class="pricing">• PRICING POLICY</span>
</div>

<form class="abs search">
  <div class="abs label" style="left:12px;top:29px">From</div>
  <div class="abs label" style="left:253px;top:29px">To</div>
  <div class="abs label" style="left:495px;top:29px">Start</div>
  <div class="abs label" style="left:638px;top:29px">Back</div>
  <div class="abs label" style="left:780px;top:29px">Adult</div>
  <div class="abs label" style="left:871px;top:29px">Child</div>
  <div class="abs field" style="left:12px;top:52px;width:220px">Select<span class="ctl"><svg width="11" height="8"><path d="M0 0h11L5.5 8z" fill="#aaa"/></svg></span></div>
  <div class="abs field" style="left:254px;top:52px;width:220px">Select<span class="ctl"><svg width="11" height="8"><path d="M0 0h11L5.5 8z" fill="#aaa"/></svg></span></div>
  <div class="abs field" style="left:496px;top:52px;width:120px;padding-left:10px">dd/mm/yy<span class="ctl" style="border:0"><svg width="18" height="17" viewBox="0 0 18 17"><rect x="1" y="2" width="16" height="14" fill="none" stroke="#333" stroke-width="1.5"/><path d="M1 6h16M5 9h2M9 9h2M13 9h2M5 12h2M9 12h2M13 12h2" stroke="#333" stroke-width="1.5"/></svg></span></div>
  <div class="abs field" style="left:638px;top:52px;width:120px;padding-left:10px">dd/mm/yy<span class="ctl" style="border:0"><svg width="18" height="17" viewBox="0 0 18 17"><rect x="1" y="2" width="16" height="14" fill="none" stroke="#333" stroke-width="1.5"/><path d="M1 6h16M5 9h2M9 9h2M13 9h2M5 12h2M9 12h2M13 12h2" stroke="#333" stroke-width="1.5"/></svg></span></div>
  <div class="abs field" style="left:780px;top:52px;width:70px">2<span class="ctl"><svg width="11" height="8"><path d="M0 0h11L5.5 8z" fill="#aaa"/></svg></span></div>
  <div class="abs field" style="left:874px;top:52px;width:70px">2<span class="ctl"><svg width="11" height="8"><path d="M0 0h11L5.5 8z" fill="#aaa"/></svg></span></div>
  <div class="abs label" style="left:12px;top:94px">Class</div>
  <div class="abs field" style="left:14px;top:116px;width:110px;height:34px">first class<span class="ctl"><svg width="11" height="8"><path d="M0 0h11L5.5 8z" fill="#aaa"/></svg></span></div>
  <div class="abs submit">SUBMIT</div>
</form>

<section class="abs feature visa">
  <div class="head"><span class="icon"><svg width="16" height="18" viewBox="0 0 16 18"><rect x="1" y="1" width="14" height="16" rx="1" fill="#ffe08a"/><path d="M5 8h6M5 11h6" stroke="#c98400" stroke-width="1.5"/></svg></span><h2>Visa</h2></div>
  <div class="rule"></div>
  <p>Sed ut perspiciatis unde omnis iste natus error sit voluptatem accusantium doloremque laudantium, totam rem aperiam, eaque ipsa quae ab illo inventore veritatis et quasi architecto beatae vitae dicta sunt explicabo. Nemo enim ipsam voluptatem quia voluptas sit aspernatur aut odit aut fugit, sed quia</p>
  <ol><li>1. VISA "ONLINE"</li><li>2. VISA "MYSELF."</li></ol>
</section>

<section class="abs feature tickets">
  <div class="head"><span class="icon"><svg width="20" height="20" viewBox="0 0 20 20"><path d="M2 11l16-7-3 4-5 1-3 6-2 0 1-5z" fill="#fff"/></svg></span><h2>Tickets</h2></div>
  <div class="rule"></div>
  <p style="text-align:left">Flights from Tours designer.</p>
  <p>On our site you can consider offers from different airlines and purchase tickets according to your wishes and budget. Plan your dates of departures and arrivals c in any country, filling the cells you want, Tour Designer automatically displays your program in the calendar. With the Tour Designer you can create any tour, including round-the-world and pay for all the services a single payment.</p>
</section>

<section class="abs feature hotels">
  <div class="head"><span class="icon"><svg width="20" height="16" viewBox="0 0 20 16"><path d="M2 2v12M2 10h16v4M6 7h12v3" stroke="#fff" stroke-width="2" fill="none"/><circle cx="4.5" cy="7.5" r="1.6" fill="#fff"/></svg></span><h2>Hotels</h2></div>
  <div class="rule"></div>
  <p style="text-align:left">Hotels by City Builder.</p>
  <p style="margin-top:18px">On our site offers a wide selection of hotels located in different countries and continents of the world. You can choose and book all kinds of accommodation options, according to your wishes and budget.</p>
  <p>Pursue their dreams!We have created for you the most convenient framework for planning a vacation or<br>business trip.</p>
</section>

<footer class="abs footer">
  <div class="abs footer-links"><a href="#">Home</a><span>|</span><a href="#">About Us</a><span>|</span><a href="#">forum</a><span>|</span><a href="#">Contacts</a><span>|</span><a href="#">help</a><span>|</span><a href="#">Terms of use</a><span>|</span><a href="#">Privacy Policy</a><span>|</span><a href="#">Cookies</a></div>
  <div class="abs copyright">Copyright © 2013 Belvasco Travel. All rights reserved.</div>
  <div class="abs social" aria-label="Social links"><span></span><span></span><span></span><span></span></div>
</footer>

</body>
</html>
```